small business website design

***Update: need the design to be coded into a wordpress or similar format***
Need a website for a small business with big plans. No online ordering etc but business description and contact details pages, a page showing products we use and page for customers or suppliers to register with us. Also want links to friendlane. We have a logo existing but also open to any improvements on the design. We have an existing website we created and looks very DIY but you can get some info from it to help create your design for us.
Updates
Hi Everyone, we didn't make it clear at the beginning but we would like the final design to be in a coded format and ready to upload to a URL. I have to apologise and admit to my lack of knowledge of the design process.
Target Market(s)
Oil / gas and industrial plant managers.
Industry/Entity Type
Small Business
Look and feel

```html
<!DOCTYPE html>
<html lang="en">
<head>
<meta charset="utf-8">
<title>Tankline Metering Co</title>
<link href="https://fonts.googleapis.com/css2?family=Open+Sans:wght@300;400;600&display=swap" rel="stylesheet">
<style>
:root{
  --blue:#2a9fd8;
  --blue-dark:#1b7fb5;
  --nav-top:#3cb3e6;
  --nav-bottom:#1f92cc;
  --text:#555;
  --heading:#333;
  --light:#f1f2f3;
  --footer:#eceef0;
  --line:#d6d8da;
  --orange:#f6bf6d;
  --teal:#5cc5c0;
  --green:#7cc47c;
  --coral:#f58b6c;
  --white:#fff;
}
*{box-sizing:border-box;margin:0;padding:0}
html,body{width:678px;height:1200px;overflow:hidden;background:var(--white);font-family:"Open Sans",Arial,sans-serif;color:var(--text)}
.page{position:relative;width:678px;height:1200px}
.abs{position:absolute}

.brand{left:48px;top:28px;display:flex;align-items:center;gap:14px}
.brand-mark{width:72px;height:72px;border-radius:50%;background:#b9bec4}
.brand-name{font-size:19px;font-weight:300;color:var(--heading);line-height:27px;width:160px}
.phone{right:38px;top:42px;font-size:14.5px;color:var(--blue);display:flex;align-items:center;gap:8px}
.search{left:482px;top:77px;width:147px;height:20px;border:1px solid var(--line);font-size:9px;color:#777;padding:4px 7px;display:flex;justify-content:space-between;align-items:center}

.nav{top:118px;left:0;width:678px;height:33px;background:linear-gradient(var(--nav-top),var(--nav-bottom));display:flex;padding-left:49px}
.nav a{color:var(--white);text-decoration:none;font-size:10px;font-weight:600;height:33px;line-height:33px;padding:0 16px;border-right:1px solid rgba(255,255,255,.25)}
.nav a.active{background:var(--blue-dark)}
.nav a:last-child{border-right:0}

.hero{top:151px;left:0;width:678px;height:242px;background:linear-gradient(#b9cbe0 0%,#e8ecef 35%,#d7dadb 55%,#6d5a45 62%,#8f7a64 78%,#c9c7c1 100%)}
.hero-arrow{width:24px;height:24px;border-radius:50%;background:rgba(140,140,140,.7);top:108px;display:flex;align-items:center;justify-content:center}
.caption{left:118px;top:150px;width:258px;height:64px;background:rgba(40,40,40,.45);padding:7px 12px;color:var(--white)}
.caption h2{font-size:13.5px;font-weight:600;margin-bottom:5px}
.caption p{font-size:7.5px;line-height:13px}

.tiles{top:430px;left:51px;width:578px;display:grid;grid-template-columns:repeat(4,1fr);grid-template-rows:111px 111px;gap:1px}
.tile{text-align:center;color:var(--white);padding-top:17px}
.tile h3{font-size:14px;font-weight:300;width:110px;margin:0 auto 7px;padding-bottom:6px;border-bottom:1px solid rgba(255,255,255,.5)}
.tile p{font-size:8px;line-height:12px;padding:0 12px}
.tile .more{display:block;font-size:8px;margin-top:10px}
.tile.orange{background:var(--orange)}
.tile.teal{background:var(--teal)}
.tile.green{background:var(--green)}
.tile.coral{background:var(--coral)}
.photo-loader{background:linear-gradient(135deg,#c6a05a,#8a5a2e 60%,#6d7f96)}
.photo-worker{background:linear-gradient(160deg,#8fb0d8,#6b7d8f 55%,#3e3a36)}
.photo-pipes{background:linear-gradient(160deg,#c9d0d8,#7e8a96 50%,#4a5561)}
.photo-gears{background:linear-gradient(135deg,#1c2229,#6f8494 50%,#27313a)}

.welcome-title{left:49px;top:697px;font-size:14.5px;color:var(--blue);font-weight:400}
.welcome-photo{left:49px;top:728px;width:140px;height:94px;background:linear-gradient(150deg,#3b4d63,#c27a2f 55%,#f3c15a 75%,#4a3a2a)}
.welcome-text{left:207px;top:727px;width:175px;font-size:7.8px;line-height:14px}
.news-title{left:49px;top:842px;font-size:14.5px;color:var(--blue);font-weight:400}
.news{left:49px;top:873px;width:334px;list-style:none}
.news li{position:relative;padding-left:15px;font-size:7.8px;line-height:12px;margin-bottom:9px}
.news li::before{content:"";position:absolute;left:1px;top:3px;width:6px;height:6px;border-radius:50%;background:#999;box-shadow:0 0 0 1px #ccc}
.news-more{left:354px;top:954px;font-size:8px;color:var(--blue)}

.contact{left:439px;top:700px;width:190px;height:264px;background:var(--light);border:1px solid #e6e7e8;padding:14px 10px}
.contact h3{font-size:14px;font-weight:400;color:var(--blue);text-align:center;margin-bottom:11px}
.field{background:var(--white);border:1px solid var(--line);height:25px;font-size:8px;color:#777;padding:7px 8px;margin-bottom:9px}
.field.message{height:66px}
.submit{display:block;margin:12px auto 0;width:137px;height:28px;background:var(--blue);border:1px solid var(--blue-dark);color:var(--white);font:400 11px "Open Sans",sans-serif}

.footer{top:1008px;left:0;width:678px;height:152px;background:var(--footer);border-bottom:1px solid var(--line)}
.badge-a{left:49px;top:1037px;width:105px;height:90px;background:#e3332f}
.badge-b{left:203px;top:1055px;width:207px;height:56px;background:#d9d9d9;border:2px solid #222}
.newsletter{left:475px;top:1030px;width:154px}
.newsletter h4{font-size:12px;font-weight:400;color:var(--heading);margin-bottom:6px}
.newsletter p{font-size:7.5px;line-height:16px;margin-bottom:6px}
.newsletter .input{height:21px;background:var(--white);border:1px solid var(--line);margin-bottom:10px}
.subscribe{margin-left:84px;width:70px;height:21px;background:var(--blue);color:var(--white);font:400 9px "Open Sans",sans-serif;border:0}
.copyright{left:50px;top:1174px;font-size:8px;color:#555}
.social{left:526px;top:1170px;display:flex;gap:4px}
.social span{width:17px;height:17px;border-radius:50%;background:#777}
</style>
</head>
<body>
<div class="page">

  <div class="abs brand">
    <div class="brand-mark"></div>
    <div class="brand-name">Tankline Metering Co</div>
  </div>
  <div class="abs phone">+61 02 5550 1234
    <svg width="13" height="15" viewBox="0 0 24 24"><path fill="#2a9fd8" d="M6.6 10.8a15 15 0 0 0 6.6 6.6l2.2-2.2c.3-.3.7-.4 1-.2 1.1.4 2.3.6 3.6.6.6 0 1 .4 1 1V20c0 .6-.4 1-1 1A17 17 0 0 1 3 4c0-.6.4-1 1-1h3.5c.6 0 1 .4 1 1 0 1.3.2 2.5.6 3.6.1.3 0 .7-.2 1z"/></svg>
  </div>
  <div class="abs search">Search..
    <svg width="8" height="8" viewBox="0 0 10 10"><circle cx="4" cy="4" r="3" fill="none" stroke="#888" stroke-width="1.3"/><path d="M6.3 6.3 9 9" stroke="#888" stroke-width="1.3"/></svg>
  </div>

  <nav class="abs nav">
    <a class="active" href="#">HOME</a>
    <a href="#">ABOUT US</a>
    <a href="#">SERVICES</a>
    <a href="#">PRODUCTS</a>
    <a href="#">NEWS &amp; EVENTS</a>
    <a href="#">TESTIMONIALS</a>
    <a href="#">CONTACT</a>
  </nav>

  <section class="abs hero" role="img" aria-label="Photo of white storage tanks at a waterside terminal">
    <div class="abs hero-arrow" style="left:48px"><svg width="8" height="10" viewBox="0 0 8 10"><path d="M6 1 2 5l4 4" fill="none" stroke="#fff" stroke-width="1.5"/></svg></div>
    <div class="abs hero-arrow" style="left:603px"><svg width="8" height="10" viewBox="0 0 8 10"><path d="m2 1 4 4-4 4" fill="none" stroke="#fff" stroke-width="1.5"/></svg></div>
    <div class="abs caption">
      <h2>Consectetuer adipisc ing elitraesent</h2>
      <p>Clantas est etiam processus dynamicus, qui sequitur mutationem consuetudium lectorum. Mirum est notare equitur.</p>
    </div>
  </section>

  <section class="abs tiles">
    <div class="photo-loader" role="img" aria-label="Photo of a wheel loader tipping earth"></div>
    <div class="tile orange"><h3>Project Support</h3><p>Maseleme leifendeuctor wisnes nera iliquam eratutpas rutrem.</p><span class="more">Read More</span></div>
    <div class="photo-worker" role="img" aria-label="Photo of a site engineer in a yellow hard hat"></div>
    <div class="tile teal"><h3>Services</h3><p>Maseleme leifendeuctor wisnes nera iliquam eratutpas rutrem.</p><span class="more">Read More</span></div>
    <div class="tile green"><h3>Our Capablities</h3><p>Maseleme leifendeuctor wisnes nera iliquam eratutpas rutrem.</p><span class="more">Read More</span></div>
    <div class="photo-pipes" role="img" aria-label="Photo of plant pipework"></div>
    <div class="tile coral"><h3>Products</h3><p>Maseleme leifendeuctor wisnes nera iliquam eratutpas rutrem.</p><span class="more">Read More</span></div>
    <div class="photo-gears" role="img" aria-label="Photo of machine gears"></div>
  </section>

  <h2 class="abs welcome-title">Welcome to Tankline Metering Co</h2>
  <div class="abs welcome-photo" role="img" aria-label="Photo of an industrial workshop with glowing metal"></div>
  <p class="abs welcome-text">Duis autem vel euim iriure dolor in hendrerit vulputate velit esse molestie consequat, vnllu m dolore eu feugiat nulla facilisis at vero eros accumsan et iusto odio dignissim qui blandpr aesent luptatum zzril delenit augue duisolore te feugait nulla facilisi. Nam liber tempor cum oluta nobis eleifend option congue.</p>

  <h2 class="abs news-title">Latest News</h2>
  <ul class="abs news">
    <li>Established in 1986 with 25 years of outstanding service, a state approved vendor</li>
    <li>A Service-Disabled Veteran-Owned company focused on hiring Service Disablietera ns, Veterans and family members of veterans</li>
    <li>As a member of the Regional Green Build Council support green design, construction and operations</li>
  </ul>
  <span class="abs news-more">More..</span>

  <form class="abs contact">
    <h3>Contact Form</h3>
    <div class="field">Name</div>
    <div class="field">Phone</div>
    <div class="field">E-mail</div>
    <div class="field message">Message</div>
    <button class="submit" type="button">Submit Request</button>
  </form>

  <footer class="abs footer"></footer>
  <div class="abs badge-a" aria-label="Partner certification badge"></div>
  <div class="abs badge-b" aria-label="Partner protocol badge"></div>
  <div class="abs newsletter">
    <h4>Newsletter</h4>
    <p>Stay in touch with us by signing up for our quarterly newsletter!</p>
    <div class="input"></div>
    <button class="subscribe" type="button">SUBSCRIBE</button>
  </div>
  <p class="abs copyright">Copyright ©2013. All Rights Reserved.</p>
  <div class="abs social" aria-label="friendlane and other social links"><span></span><span></span><span></span><span></span></div>

</div>
</body>
</html>
```